UI/UX Re-Do for TallyNest - a free to use project management platform for desktop and mobile.

UI/UX Re-Do for TallyNest
TallyNest is a free to use project management platform for desktop and mobile.
We are looking for help with our UI/UX re-design.
As of now the platform is totally functional.
The problem is around flow and look. We want TN to become something that any one can use to manage and even socialize any project. A project can be something work related like organizing a team around a software build, marketing campaign, shared client file space, etc... In fact, most of our current members are using TN for just such work projects.
We also see a project as planning a wedding, organizing a group trip, a simple to-do list, organizing a kids sports team, and so on...
To become a platform that people will use in their work and personal life we first need to become more intuitive and friendly - while maintaining advanced functionality for more advanced needs.
We need help to beautify, streamline, and simplify - while keeping all the functions.
The quickest way to understand TN, and our current issues is this short video:
https://vidlumo.example/w/Qa7KdP2mXzR
For sure see this link for the entire most recent description AND images:
https://tallynestapp.example/?p=HumbZ4KcWrT
The best way to understand TN is to actually use it:
https://tallynestapp.example
Should you choose to take a run at improving TN here are the details:
Please focus your ideas for mobile, it's where we have the biggest issues.
Feel free to get outside the box.
Avoid swipe oriented designs.
Feel free to focus on ideas over polished outputs.
Use any tool you like, PS, hand drawing, written description if you think that works best.
(FYI - we use mostly use Orvane Slides docs internally)
Point is illustration of ideas over tool choice.
Feel free to:
Create something totally new
And/or riff on what we have now
And/or riff on the new design we are considering (see images below)
|||
If we go the direction of the images/designs below the idea is to give people options on how they see/experience TN.
Just below is what we are calling Ground View. This is a more basic and simple flow. Probably a default to keep new users feeling comfortable at the start.
<img src="https://i.picbarn.example/8wNtLQe.jpg" style="width: 100%;">
https://i.picbarn.example/8wNtLQe.jpg
|||
We are calling this optional view Sky View. It is more advanced and can show all project, goal(renamed 'milestones') at the same time. This is more of a paint job on the current design.
<img src="https://i.picbarn.example/vhRmJxd.jpg" style="width: 100%;">
https://i.picbarn.example/vhRmJxd.jpg
|||
If you're submitting please let us know if you can also do the PS files for dev.
Not required, but once we nail down the concepts we want someone to hone in the PS files.
As an optional bonus we will also be giving credit to you/your company in TN.
Let us know if you do or don't want that.
We are excited to see your work!!
<img src=" " style="width: 100%;">
Target Market(s)
Anyone who needs to organize any project, big or small. The key is to make a super friendly user experience for new users while retaining advanced functions.
Industry/Entity Type
Management
Number of Pages Required
2 page

```html
<!DOCTYPE html>
<html lang="en">
<head>
<meta charset="utf-8">
<title>TallyNest – Shared Project</title>
<link href="https://fonts.googleapis.com/css2?family=Roboto:wght@300;400;500&display=swap" rel="stylesheet">
<style>
:root{
  --bg:#f5f7f9;--dark:#06202a;--search:#5c6b70;--orange:#ff8a00;--blue:#2a93b8;
  --grey:#6b6b6b;--line:#e2e5e8;--text:#333;--muted:#8a8f93;--white:#fff;
}
*{box-sizing:border-box;margin:0;padding:0}
html,body{width:1200px;height:1059px;overflow:hidden}
body{background:var(--bg);font-family:'Roboto',Arial,sans-serif;color:var(--text);position:relative}
.abs{position:absolute}
.topbar{left:0;top:0;width:1200px;height:56px;background:var(--dark)}
.brand{left:21px;top:7px;width:43px;height:43px;border-radius:50%;background:#000;color:var(--orange);font-size:20px;display:flex;align-items:center;justify-content:center}
.menu{left:78px;top:19px}
.search{left:108px;top:9px;width:998px;height:36px;background:var(--search)}
.search svg{position:absolute;left:13px;top:11px}
.views{right:14px;top:16px;display:flex;gap:11px}
.sidebar{left:14px;top:105px;width:342px;height:846px;background:var(--white)}
.scroll-track{left:369px;top:105px;width:12px;height:846px;background:#f0f0f0;border:1px solid var(--line)}
.scroll-thumb{left:2px;top:14px;width:7px;height:255px;background:#c8c8c8}
.section-head{left:0;width:342px;height:45px;display:flex;align-items:center;color:var(--white);font-size:14.5px;font-weight:500;white-space:nowrap}
.section-head .ico{width:42px;display:flex;justify-content:center;border-right:1px solid rgba(255,255,255,.5);margin-right:13px;height:16px;align-items:center}
.section-head.orange{background:var(--orange);top:0}
.section-head.grey{background:var(--grey)}
.item{left:13px;width:329px;height:51px;background:var(--white);border:1px solid var(--line);border-left:5px solid var(--blue)}
.item.active{border-left-color:var(--orange)}
.item .icon{position:absolute;left:10px;top:12px;width:26px;height:26px}
.item .title{position:absolute;left:59px;top:11px;font-size:11.8px;font-weight:500;color:#333;letter-spacing:-.15px;white-space:nowrap}
.item .status{position:absolute;left:59px;top:30px;font-size:12.2px;color:var(--muted)}
.pill{position:absolute;right:10px;top:13px;width:52px;height:24px;border:1px solid #ccd;border-radius:12px;display:flex;align-items:center;justify-content:space-around;padding:0 6px;background:var(--white)}
.under{left:28px;width:298px;height:3px;border:1px solid var(--line);border-top:none}
.actions{left:28px;top:118px;width:298px;height:29px;border:1px solid var(--line);display:flex;background:var(--white)}
.actions div{flex:1;display:flex;align-items:center;justify-content:center;gap:6px;font-size:10px;color:#666;border-right:1px solid var(--line);white-space:nowrap}
.actions div:last-child{border-right:none}
.card{left:417px;top:105px;width:761px;height:358px;background:var(--white);border:1px solid var(--line)}
.card-head{left:0;top:0;width:759px;height:52px;background:var(--blue);color:var(--white)}
.avatar{left:15px;top:6px;width:39px;height:39px;border-radius:50%;background:#1c6f8c;display:flex;align-items:center;justify-content:center;font-size:14px;font-weight:500}
.card-title{left:72px;top:9px;font-size:15.5px;font-weight:500;white-space:nowrap}
.card-date{left:73px;top:31px;font-size:12px;opacity:.9}
.kebab{right:22px;top:20px}
.card-body{left:24px;top:86px;width:714px;font-size:12.2px;font-weight:300;line-height:25.7px;color:#666}
.tmp-title{left:25px;top:215px;font-size:12.6px;font-weight:500;color:#444;white-space:nowrap}
.tmp-link{left:25px;top:240px;font-size:11.8px;color:var(--blue);text-decoration:underline;white-space:nowrap}
.btn{top:280px;height:43px;width:114px;color:var(--white);font-size:14px;font-weight:500;display:flex;align-items:center;justify-content:center}
.btn.more{left:261px;background:var(--orange)}
.btn.close{left:384px;background:var(--blue)}
.card-scroll{left:746px;top:54px;width:13px;height:302px;background:#f2f2f2}
.card-scroll div{position:absolute;left:2px;top:18px;width:9px;height:175px;background:#c8c8c8}
.feed{left:417px;top:481px;width:761px;height:202px;background:var(--white);border:1px solid var(--line)}
.composer{left:417px;top:695px;width:761px;height:46px;background:var(--white);border:1px solid var(--line)}
.composer .ph{position:absolute;left:19px;top:15px;font-size:12.5px;color:#555}
.composer .tools{position:absolute;right:0;top:0;height:44px;display:flex}
.composer .tools div{width:43px;border-left:1px solid var(--line);display:flex;align-items:center;justify-content:center}
.footer{left:0;top:997px;width:1200px;height:62px;background:var(--dark);color:var(--white);font-size:12.5px;display:flex;align-items:center;justify-content:center}
</style>
</head>
<body>
<header class="abs topbar">
  <div class="abs brand">TN</div>
  <svg class="abs menu" width="18" height="15" viewBox="0 0 18 15"><rect width="18" height="3" fill="#fff"/><rect y="6" width="18" height="3" fill="#fff"/><rect y="12" width="18" height="3" fill="#fff"/></svg>
  <div class="abs search"><svg width="14" height="14" viewBox="0 0 14 14"><circle cx="6" cy="6" r="4.5" stroke="#fff" stroke-width="2" fill="none"/><line x1="9.5" y1="9.5" x2="13" y2="13" stroke="#fff" stroke-width="2"/></svg></div>
  <div class="abs views">
    <svg width="33" height="21" viewBox="0 0 33 21"><rect width="8" height="21" rx="3" fill="#ddd"/><rect x="11" width="22" height="21" rx="3" fill="#ddd"/></svg>
    <svg width="27" height="21" viewBox="0 0 27 21"><rect width="7" height="21" rx="3" fill="#ddd"/><rect x="10" width="7" height="21" rx="3" fill="#ddd"/><rect x="20" width="7" height="21" rx="3" fill="#ddd"/></svg>
  </div>
</header>

<aside class="abs sidebar">
  <div class="abs section-head orange"><span class="ico"><svg width="20" height="14" viewBox="0 0 20 14"><polyline points="1,13 6,7 10,10 18,2" stroke="#fff" stroke-width="2" fill="none"/><polyline points="1,1 1,13 19,13" stroke="#fff" stroke-width="1.5" fill="none"/></svg></span>CURRENT SHARED PROJECT</div>

  <div class="abs item active" style="top:66px">
    <svg class="icon" viewBox="0 0 28 28"><path d="M24 3c-6 0-11 4-14 9l-4 1-3 4 5-1 3 3-1 5 4-3 1-4c5-3 9-8 9-14z" fill="#ff6a00"/><circle cx="18" cy="10" r="2" fill="#fff"/></svg>
    <span class="title">STARTUP STARTER KIT</span><span class="status">Status</span>
    <span class="pill"><svg width="14" height="9" viewBox="0 0 14 9"><ellipse cx="7" cy="4.5" rx="7" ry="4.5" fill="#ff8a00"/><circle cx="7" cy="4.5" r="2" fill="#fff"/></svg><svg width="6" height="9" viewBox="0 0 6 9"><polyline points="1,1 5,4.5 1,8" stroke="#ff8a00" fill="none" stroke-width="1.3"/></svg></span>
  </div>
  <div class="abs actions">
    <div><svg width="7" height="5"><polygon points="0,5 3.5,0 7,5" fill="#777"/></svg>HIDE GOALS</div>
    <div><svg width="4" height="9"><rect x="1" y="3" width="2" height="6" fill="#777"/><rect x="1" width="2" height="2" fill="#777"/></svg>JOIN</div>
    <div><svg width="9" height="11"><rect x=".5" y=".5" width="8" height="10" fill="none" stroke="#777"/><line x1="2" y1="5" x2="7" y2="5" stroke="#777"/><line x1="2" y1="7" x2="7" y2="7" stroke="#777"/></svg>COPY</div>
  </div>

  <div class="abs item" style="top:171px"><svg class="icon" viewBox="0 0 28 28"><circle cx="7" cy="6" r="3" fill="#2a93b8"/><circle cx="14" cy="5" r="3" fill="#2a93b8"/><circle cx="21" cy="6" r="3" fill="#2a93b8"/><rect x="3" y="11" width="22" height="8" fill="#2a93b8"/><rect x="5" y="19" width="4" height="7" fill="#2a93b8"/><rect x="19" y="19" width="4" height="7" fill="#2a93b8"/></svg><span class="title">MEETING NOTES / BUSINESS SCRUM</span><span class="status">Status</span><span class="pill"><svg width="14" height="9"><ellipse cx="7" cy="4.5" rx="7" ry="4.5" fill="#2a93b8"/><circle cx="7" cy="4.5" r="2" fill="#fff"/></svg><svg width="6" height="9"><polyline points="1,1 5,4.5 1,8" stroke="#2a93b8" fill="none" stroke-width="1.3"/></svg></span></div>
  <div class="abs under" style="top:222px"></div>

  <div class="abs item" style="top:246px"><svg class="icon" viewBox="0 0 28 28"><rect x="11" y="3" width="6" height="6" fill="#2a93b8"/><rect x="13" y="9" width="2" height="6" fill="#2a93b8"/><rect x="4" y="14" width="20" height="2" fill="#2a93b8"/><rect x="2" y="19" width="6" height="6" fill="#2a93b8"/><rect x="11" y="19" width="6" height="6" fill="#2a93b8"/><rect x="20" y="19" width="6" height="6" fill="#2a93b8"/></svg><span class="title">CORPORATE STRUCTURE</span><span class="status">Status</span><span class="pill"><svg width="14" height="9"><ellipse cx="7" cy="4.5" rx="7" ry="4.5" fill="#2a93b8"/><circle cx="7" cy="4.5" r="2" fill="#fff"/></svg><svg width="6" height="9"><polyline points="1,1 5,4.5 1,8" stroke="#2a93b8" fill="none" stroke-width="1.3"/></svg></span></div>
  <div class="abs under" style="top:297px"></div>

  <div class="abs item" style="top:322px"><svg class="icon" viewBox="0 0 28 28"><circle cx="14" cy="17" r="10" fill="#2a93b8"/><rect x="10" y="3" width="8" height="4" fill="#2a93b8"/><text x="14" y="22" text-anchor="middle" font-size="13" font-family="Roboto,sans-serif" fill="#fff">$</text></svg><span class="title">FUND RAISING / CORP DEV</span><span class="status">Status</span><span class="pill"><svg width="14" height="9"><ellipse cx="7" cy="4.5" rx="7" ry="4.5" fill="#2a93b8"/><circle cx="7" cy="4.5" r="2" fill="#fff"/></svg><svg width="6" height="9"><polyline points="1,1 5,4.5 1,8" stroke="#2a93b8" fill="none" stroke-width="1.3"/></svg></span></div>
  <div class="abs under" style="top:373px"></div>

  <div class="abs item" style="top:395px"><svg class="icon" viewBox="0 0 28 28"><circle cx="14" cy="14" r="7" fill="none" stroke="#2a93b8" stroke-width="2.5"/><polygon points="22,2 26,8 18,8" fill="#2a93b8"/><polygon points="6,26 2,20 10,20" fill="#2a93b8"/></svg><span class="title">OPERATING FINANCE</span><span class="status">Status</span><span class="pill"><svg width="14" height="9"><ellipse cx="7" cy="4.5" rx="7" ry="4.5" fill="#2a93b8"/><circle cx="7" cy="4.5" r="2" fill="#fff"/></svg><svg width="6" height="9"><polyline points="1,1 5,4.5 1,8" stroke="#2a93b8" fill="none" stroke-width="1.3"/></svg></span></div>
  <div class="abs under" style="top:446px"></div>

  <div class="abs item" style="top:468px"><svg class="icon" viewBox="0 0 28 28"><circle cx="14" cy="14" r="10" fill="none" stroke="#2a93b8" stroke-width="3" stroke-dasharray="4 2"/><circle cx="14" cy="14" r="4" fill="#2a93b8"/></svg><span class="title">SALE / BUSINESS DEVELOPMENT</span><span class="status">Status</span><span class="pill"><svg width="14" height="9"><ellipse cx="7" cy="4.5" rx="7" ry="4.5" fill="#2a93b8"/><circle cx="7" cy="4.5" r="2" fill="#fff"/></svg><svg width="6" height="9"><polyline points="1,1 5,4.5 1,8" stroke="#2a93b8" fill="none" stroke-width="1.3"/></svg></span></div>
  <div class="abs under" style="top:519px"></div>

  <div class="abs item" style="top:540px"><svg class="icon" viewBox="0 0 28 28"><polygon points="3,12 18,5 18,22 3,17" fill="#2a93b8"/><rect x="6" y="17" width="4" height="7" fill="#2a93b8"/><path d="M21 9q3 4 0 8" stroke="#2a93b8" stroke-width="2" fill="none"/></svg><span class="title">MARKETING</span><span class="status">Status</span><span class="pill"><svg width="14" height="9"><ellipse cx="7" cy="4.5" rx="7" ry="4.5" fill="#2a93b8"/><circle cx="7" cy="4.5" r="2" fill="#fff"/></svg><svg width="6" height="9"><polyline points="1,1 5,4.5 1,8" stroke="#2a93b8" fill="none" stroke-width="1.3"/></svg></span></div>
  <div class="abs under" style="top:591px"></div>

  <div class="abs item" style="top:614px"><svg class="icon" viewBox="0 0 28 28"><rect x="12" y="5" width="4" height="18" fill="#2a93b8"/><rect x="5" y="12" width="18" height="4" fill="#2a93b8"/></svg><span class="title">OTHER</span><span class="status">Status</span><span class="pill"><svg width="14" height="9"><ellipse cx="7" cy="4.5" rx="7" ry="4.5" fill="#2a93b8"/><circle cx="7" cy="4.5" r="2" fill="#fff"/></svg><svg width="6" height="9"><polyline points="1,1 5,4.5 1,8" stroke="#2a93b8" fill="none" stroke-width="1.3"/></svg></span></div>
  <div class="abs under" style="top:665px"></div>

  <div class="abs section-head grey" style="top:695px"><span class="ico"><svg width="16" height="16" viewBox="0 0 16 16"><path d="M1 8a7 6 0 0114 0z" fill="#fff"/><path d="M8 8v6a2 2 0 01-3 0" stroke="#fff" stroke-width="1.5" fill="none"/></svg></span>TALLYNEST TOP PROJECT PICKS</div>
  <div class="abs section-head grey" style="top:747px"><span class="ico"><svg width="14" height="18" viewBox="0 0 14 18"><path d="M1 1h8l4 4v12H1z" stroke="#fff" stroke-width="1.4" fill="none"/><line x1="4" y1="9" x2="10" y2="9" stroke="#fff"/><line x1="4" y1="12" x2="10" y2="12" stroke="#fff"/></svg></span>MOST POPULAR PUBILC PROJECTS</div>
  <div class="abs section-head grey" style="top:801px"><span class="ico"><svg width="16" height="16" viewBox="0 0 16 16"><polygon points="11,1 15,5 5,15 1,15 1,11" fill="#fff"/></svg></span>ALL PUBILC PROJECTS</div>
</aside>
<div class="abs scroll-track"><div class="abs scroll-thumb"></div></div>

<main>
  <section class="abs card">
    <div class="abs card-head">
      <div class="abs avatar">TN</div>
      <div class="abs card-title">DORIAN VALE TN CASES</div>
      <div class="abs card-date">6/1/2017 6:36 am IST</div>
      <svg class="abs kebab" width="4" height="14"><circle cx="2" cy="2" r="1.8" fill="#fff"/><circle cx="2" cy="7" r="1.8" fill="#fff"/><circle cx="2" cy="12" r="1.8" fill="#fff"/></svg>
    </div>
    <p class="abs card-body">Welcome to the TallyNest 'Startup Starter Kit' - do more better! We the team at TallyNest have been used the assets and structure in this kit across several startups. Most of what you will find here are things that will help you get started in your earliest phases. We recommend you look though the structure of this project as a an organizational logic, and then dig into some of the documentation templates. Best of luck on your venture, and please let us know if we can help!</p>
    <div class="abs tmp-title">TMP - GENERAL BUSINESS SCRUM TEMPLATE</div>
    <div class="abs tmp-link">https://docs.orvane.example/document/d/7pRtLmQwZ4sXn9KbVc2HfJ8aYe3NdG6uTo1WkRs5Mz/edit</div>
    <div class="abs btn more">VIEW MORE</div>
    <div class="abs btn close">CLOSE</div>
    <div class="abs card-scroll"><div></div></div>
  </section>
  <section class="abs feed"></section>
  <div class="abs composer">
    <span class="ph">Type Here....</span>
    <div class="tools">
      <div><svg width="16" height="14"><ellipse cx="8" cy="6" rx="7" ry="5" fill="none" stroke="#ff8a00" stroke-width="1.4"/><path d="M4 10l-2 3 5-2" fill="#ff8a00"/></svg></div>
      <div><svg width="16" height="16"><circle cx="5" cy="5" r="3" fill="none" stroke="#ff8a00" stroke-width="1.6"/><circle cx="11" cy="11" r="3" fill="none" stroke="#ff8a00" stroke-width="1.6"/><line x1="7" y1="7" x2="9" y2="9" stroke="#ff8a00" stroke-width="1.6"/></svg></div>
      <div><svg width="16" height="14"><rect x="1" y="3" width="14" height="10" rx="2" fill="#ff8a00"/><rect x="5" y="1" width="6" height="3" fill="#ff8a00"/><circle cx="8" cy="8" r="3" fill="#fff"/></svg></div>
      <div><svg width="13" height="16"><path d="M1 1h7l4 4v10H1z" fill="none" stroke="#ff8a00" stroke-width="1.4"/></svg></div>
    </div>
  </div>
</main>

<footer class="abs footer">© Copy Right 2017 TallyNest App. All rights reserved.</footer>
</body>
</html>
```